Business Report Cover

We need a revamped quarterly report cover to send to our clients. We asset manage commercial and residential properties throughout the the United States. We use a .pdf version of a cover that we've used for years but would like a fresh updated look for 2018. The cover should include our company logo (KOV Enterprises) and a photo of the property as well as the Quarter/Year of the report.

```html
<!DOCTYPE html>
<html lang="en">
<head>
<meta charset="utf-8">
<title>KOV Enterprises – Quarterly Operating Report Q1 2018</title>
<link rel="stylesheet" href="https://fonts.googleapis.com/css2?family=Encode+Sans+Condensed:wght@400;500;700&display=swap">
<style>
  :root {
    --brand-green: #0b7339;
    --charcoal: #333333;
    --paper: #ffffff;
    --backdrop: #e9e9e7;
    --ink: #1a1a1a;
    --text-light: #ffffff;
  }
  * { margin: 0; padding: 0; box-sizing: border-box; }
  html, body {
    width: 1200px; height: 1200px; overflow: hidden;
    background: var(--backdrop);
    font-family: "Encode Sans Condensed", "Arial Narrow", sans-serif;
  }
  .canvas {
    position: relative; width: 1200px; height: 1200px;
  }
  .report-cover {
    position: absolute;
    left: 175px; top: 0;
    width: 985px; height: 1391px;
    background: var(--paper);
    transform: scale(0.8627);
    transform-origin: 0 0;
    overflow: hidden;
  }
  .cover-shapes {
    position: absolute; inset: 0;
    width: 985px; height: 1391px;
  }
  .shape-charcoal { fill: var(--charcoal); }
  .shape-green { fill: var(--brand-green); }
  .title-band { fill: var(--charcoal); opacity: 0.92; }

  .brand-name {
    position: absolute;
    right: 72px; top: 140px;
    text-align: right;
    color: var(--ink);
    font-weight: 700;
    line-height: 1;
  }
  .brand-name .brand-main {
    display: block;
    font-size: 104px;
    letter-spacing: -1px;
  }
  .brand-name .brand-sub {
    display: block;
    margin-top: 6px;
    font-size: 22px;
    letter-spacing: 8px;
    margin-right: -8px;
  }

  .report-title {
    position: absolute;
    left: 133px; top: 962px;
    color: var(--text-light);
    font-weight: 400;
    font-size: 40px;
    line-height: 50px;
    letter-spacing: -0.5px;
  }
  .report-year {
    position: absolute;
    left: 124px; top: 1095px;
    color: var(--brand-green);
    font-weight: 500;
    font-size: 118px;
    line-height: 1;
    letter-spacing: -2px;
  }
  .property-footer {
    position: absolute;
    left: 0; bottom: 0;
    width: 100%; height: 66px;
    background: var(--charcoal);
    color: var(--text-light);
    font-size: 22px;
    display: flex; align-items: center; justify-content: center;
  }
</style>
</head>
<body>
<div class="canvas">
  <section class="report-cover">
    <svg class="cover-shapes" viewBox="0 0 985 1391" xmlns="http://www.w3.org/2000/svg">
      <defs>
        <linearGradient id="propertyTones" x1="0" y1="0" x2="0" y2="1">
          <stop offset="0" stop-color="#c9ccd3"/>
          <stop offset="0.38" stop-color="#aeb1b8"/>
          <stop offset="0.55" stop-color="#6b4a40"/>
          <stop offset="0.75" stop-color="#4a4a52"/>
          <stop offset="1" stop-color="#3b3638"/>
        </linearGradient>
      </defs>
      <polygon class="shape-charcoal" points="0,0 238,0 0,590"/>
      <polygon class="shape-green" points="265,0 381,0 113,665 0,665 0,658"/>
      <polygon role="img" aria-label="Photo of the convenience store property with fuel canopy and pumps"
               fill="url(#propertyTones)" points="335,324 985,324 985,1006 60,1006"/>
      <polygon class="shape-green" points="0,938 88,938 28,1078 0,1078"/>
      <polygon class="title-band" points="88,938 690,938 643,1078 28,1078"/>
      <polygon class="shape-green" points="778,938 868,938 813,1078 725,1078"/>
    </svg>

    <div class="brand-name">
      <span class="brand-main">KOV</span>
      <span class="brand-sub">ENTERPRISES</span>
    </div>

    <h1 class="report-title">QUARTERLY OPERATING REPORT<br>1ST QUARTER</h1>
    <div class="report-year">2018</div>

    <footer class="property-footer">Riverton Corner Mart&nbsp; 4120 NE Harbor Plaza Dr. Riverton, WA 98610</footer>
  </section>
</div>
</body>
</html>
```